Timber Crest Construction Needs business card

Hey we are in need of business card designs. I have upload our logo as a guideline, but free feel to run with it or come up with something unique.
Pls have fun with it and be creative. the name says it all!
i will give some directions after i see a few entries..
Updates
Logo source file has been uploaded..
Hey because of the logo is so colourful already.
Can we have a few submissions with less colour.
Also we are looking for clever/hidden/descriptive business card.

```html
<!DOCTYPE html>
<html lang="en">
<head>
<meta charset="utf-8">
<title>Timber Crest Construction – Business Card</title>
<link rel="stylesheet" href="https://fonts.googleapis.com/css2?family=Questrial&family=Mulish:wght@700;800&display=swap">
<style>
  :root {
    --stage: #1f7d06;
    --card-dark: #000000;
    --card-light: #ffffff;
    --brand-grey: #8a8a8a;
    --ink: #2b2b2b;
    --accent-red: #e3282d;
    --decor-grey: #e2e2e2;
  }
  * { margin: 0; padding: 0; box-sizing: border-box; }
  html, body {
    width: 1200px; height: 1200px; overflow: hidden;
    background: var(--stage);
    font-family: "Questrial", "Century Gothic", sans-serif;
  }
  .canvas { position: relative; width: 1200px; height: 1200px; }

  .card { position: absolute; left: 212px; width: 800px; height: 445px; }
  .card-front { top: 130px; background: var(--card-dark); }
  .card-back { top: 641px; background: var(--card-light); overflow: hidden; }

  .brand-name {
    color: var(--brand-grey);
    font-family: "Questrial", sans-serif;
    font-weight: 400;
    text-transform: uppercase;
    line-height: 1;
  }
  .brand-name .brand-main { display: block; font-size: 44px; letter-spacing: 1px; }
  .brand-name .brand-sub { display: block; font-size: 15px; letter-spacing: 1.5px; margin-top: 4px; }

  .card-front .brand-name {
    position: absolute; left: 0; right: 0; top: 186px; text-align: center;
  }
  .card-back .brand-name {
    position: absolute; left: 87px; top: 76px;
  }
  .card-back .brand-name .brand-sub { padding-left: 104px; }

  .person {
    position: absolute; left: 87px; top: 184px;
    font-size: 15px; letter-spacing: 4px; color: var(--ink);
  }
  .person-name { font-family: "Mulish", sans-serif; font-weight: 800; }
  .person-sep { margin: 0 6px; color: var(--ink); }
  .person-role { color: var(--accent-red); }

  .address {
    position: absolute; left: 87px; top: 237px;
    font-size: 13.5px; letter-spacing: 2.6px; line-height: 21px;
    color: var(--ink); text-transform: uppercase;
  }

  .contacts {
    position: absolute; left: 87px; top: 297px; list-style: none;
  }
  .contacts li {
    display: flex; align-items: center; height: 25.3px;
    font-size: 14px; letter-spacing: 2.2px; color: var(--ink);
  }
  .contacts svg { width: 15px; height: 15px; margin-right: 21px; flex: none; }
  .icon-stroke { fill: none; stroke: var(--accent-red); stroke-width: 1.4; }
  .icon-fill { fill: var(--accent-red); }

  .decor-building {
    position: absolute; left: 454px; top: 148px; width: 346px; height: 297px;
    background: linear-gradient(160deg, #e8e8e8 0%, var(--decor-grey) 60%, #dadada 100%);
  }
</style>
</head>
<body>
<main class="canvas">
  <section class="card card-front" aria-label="Card front">
    <h1 class="brand-name">
      <span class="brand-main">Timber Crest</span>
      <span class="brand-sub">Construction</span>
    </h1>
  </section>

  <section class="card card-back" aria-label="Card back">
    <div class="brand-name">
      <span class="brand-main">Timber Crest</span>
      <span class="brand-sub">Construction</span>
    </div>

    <p class="person">
      <span class="person-name">MAREK DALTON</span><span class="person-sep">-</span><span class="person-role">DIRECTOR</span>
    </p>

    <p class="address">Shop 2, 318-322 Harbour<br>Road Kingsford West</p>

    <ul class="contacts">
      <li>
        <svg viewBox="0 0 16 16" aria-hidden="true"><path class="icon-fill" d="M2 6c0-2 2.5-3 6-3s6 1 6 3v1h-3V5.5H5V7H2z"/><path class="icon-fill" d="M4 8h8l1 5H3z"/></svg>
        9481 2075
      </li>
      <li>
        <svg viewBox="0 0 16 16" aria-hidden="true"><rect class="icon-stroke" x="4.5" y="1.5" width="7" height="4"/><rect class="icon-stroke" x="1.5" y="5.5" width="13" height="6"/><rect class="icon-stroke" x="4.5" y="9.5" width="7" height="5"/></svg>
        9481 2093
      </li>
      <li>
        <svg viewBox="0 0 16 16" aria-hidden="true"><rect class="icon-stroke" x="1.5" y="3.5" width="13" height="9"/><path class="icon-stroke" d="M1.5 3.5L8 9l6.5-5.5"/></svg>
        marek@timbercrestbuild.com
      </li>
      <li>
        <svg viewBox="0 0 16 16" aria-hidden="true"><circle class="icon-stroke" cx="8" cy="8" r="6.5"/><ellipse class="icon-stroke" cx="8" cy="8" rx="2.8" ry="6.5"/><path class="icon-stroke" d="M1.5 8h13M2.5 4.8h11M2.5 11.2h11"/></svg>
        www.timbercrestbuild.com
      </li>
    </ul>

    <div class="decor-building" role="img" aria-label="Faint grey building decoration"></div>
  </section>
</main>
</body>
</html>
```